Medical Skincare services/menu/pricing Booklet 12 pages

We need produce a 12-page glossy, saddle-stitched booklet (5 1/2" tall X 81/2" wide). The booklet will be used as a services menu for a skin care salon. I have mocked up the booklet (w/ all copy) in WORD and I've provided a separate PDF of the accurate page order (see files attached). IMPORTANT: Feel free to use your creativity yet style-wise it should kinda match my wife's website colors and text style. Her clients are demanding so she wants a clean, high end, modern look (ala Apple maybe?). See her website for a frame of reference www.GlowWithMara.com
Updates

Target Market(s)

upscale female, professional women, teens with acne

Industry/Entity Type

Medical

Requirements
Must have
• the pics in the mock up are important. I've attached them here

```html
<!DOCTYPE html>
<html lang="en">
<head>
<meta charset="utf-8">
<title>Services Booklet – About &amp; Testimonials Spread</title>
<link rel="stylesheet" href="https://fonts.googleapis.com/css2?family=Open+Sans:wght@300;400;600;700&display=swap">
<style>
  :root {
    --bg: #9a9a9a;
    --paper: #ffffff;
    --paper-shade: #f1f1f1;
    --panel: rgba(18, 18, 18, 0.9);
    --panel-text: #e6e6e6;
    --ink: #3a3a3a;
    --ink-strong: #1e1e1e;
    --quote-mark: #d2d2d2;
    --rule: #555555;
    --photo-a: #b9ad95;
    --photo-b: #7c8a83;
    --photo-c: #4e5a50;
  }
  * { box-sizing: border-box; margin: 0; padding: 0; }
  html, body { width: 1200px; height: 900px; overflow: hidden; }
  body {
    background: var(--bg);
    font-family: "Open Sans", sans-serif;
    position: relative;
  }
  .spread {
    position: absolute;
    left: 40px; top: 269px;
    width: 1120px; height: 362px;
    display: flex;
    box-shadow: 0 14px 30px rgba(0,0,0,0.25);
  }
  .page { position: relative; width: 560px; height: 362px; overflow: hidden; background: var(--paper); }

  /* Left page */
  .about-photo {
    position: absolute; left: 0; top: 0; width: 78%; height: 100%;
    background: linear-gradient(160deg, var(--photo-a) 0%, var(--photo-b) 55%, var(--photo-c) 100%);
  }
  .about-panel {
    position: absolute; left: 46%; top: 34px; right: 0; bottom: 44px;
    background: var(--panel);
    color: var(--panel-text);
    padding: 14px 18px 12px 20px;
  }
  .about-name {
    font-weight: 300; font-size: 12px; letter-spacing: 0.3px; text-transform: uppercase;
    color: #fff; margin-bottom: 6px;
  }
  .about-name small { font-size: 7.5px; font-weight: 400; }
  .about-body { font-size: 7px; line-height: 10.4px; text-align: justify; margin-bottom: 8px; }
  .about-body strong { font-weight: 600; }

  /* Right page */
  .testimonials { background: linear-gradient(90deg, var(--paper-shade) 0%, var(--paper) 6%); }
  .bg-arc {
    position: absolute; border-radius: 50%; background: #f4f4f4;
  }
  .section-title {
    position: absolute; left: 52px; top: 36px;
    font-weight: 300; font-size: 15px; letter-spacing: 0.3px; color: var(--ink-strong);
    padding-bottom: 4px; border-bottom: 1.5px solid var(--rule); width: 92px;
  }
  .quote { position: absolute; width: 190px; font-size: 7.3px; line-height: 10.5px; color: var(--ink); }
  .quote .mark {
    position: absolute; font-size: 44px; line-height: 1; color: var(--quote-mark); font-weight: 700;
  }
  .quote .open { left: -6px; top: -28px; }
  .quote .close { right: -22px; bottom: -30px; }
  .quote cite {
    display: block; font-style: normal; font-weight: 700; font-size: 7px; color: var(--ink-strong);
    text-align: right; margin-top: 6px; line-height: 9.5px;
  }
</style>
</head>
<body>
  <div class="spread">
    <section class="page about">
      <div class="about-photo" role="img" aria-label="Photo of the aesthetician standing in a long patterned dress beside columns and potted flowers"></div>
      <div class="about-panel">
        <h2 class="about-name">Mara Vidal <small>(Medical Aesthetician &amp; Owner)</small></h2>
        <p class="about-body">As a teenager, I had cystic acne so bad that I would ditch school to swim in the ocean because the saltwater seemed to dry out and heal my skin. I was on such a mission to clear my skin that I spent my weekly allowance on skin care products I saw on TV. Then, I memorized every ingredient. I was so intrigued by the beauty industry that, by 19, I began a career as a make up artist for Lumière, Velvet, Bellarosa, Formula and Stelle. By 23, I was a skincare consultant for the Harlow Klein Salons in Bellmont Hills and Seacrest County. I was honored to learn from the world's most demanding clients.</p>
        <p class="about-body"><strong>I Understand Why Your Skin Matters.</strong> Admit it. We take more pictures of ourselves than ever… and then try to "fix" our blemishes with photo filters. I understand your frustrations. Some of you know I've had a parallel career as a professional singer who does network TV appearances, where the HD cameras get extreme close ups. Yikes! I also sing the National Anthem at national pro football, basketball and baseball games, where their 200 foot-wide stadium screens constantly remind me that skin imperfections are magnified. I will help get your skin more naturally beautiful so you can use less photo filters ;)</p>
      </div>
    </section>

    <section class="page testimonials">
      <div class="bg-arc" style="left:250px; top:-160px; width:380px; height:380px;"></div>
      <div class="bg-arc" style="left:-120px; top:170px; width:330px; height:330px; background:#f7f7f7;"></div>

      <h2 class="section-title">Testimonials</h2>

      <blockquote class="quote" style="left:330px; top:40px; width:200px;">
        <span class="mark open">&ldquo;</span>
        I have been seeing Mara Vidal for her signature facials. Ever since my first Aquafacial my skin has had a healthy glow and texture. As an Aesthetic Professional, she helps me feel my personal best.
        <cite>DANA WHITFIELD, R. N.</cite>
        <span class="mark close">&rdquo;</span>
      </blockquote>

      <blockquote class="quote" style="left:62px; top:118px;">
        <span class="mark open">&ldquo;</span>
        Mara is someone I definitely trust with my skincare needs because she truly cares about people and their issues.
        <cite>COLETTE RAMSEY<br>Reality TV star/Coastal Living Series</cite>
        <span class="mark close">&rdquo;</span>
      </blockquote>

      <blockquote class="quote" style="left:320px; top:128px; width:200px;">
        <span class="mark open">&ldquo;</span>
        I have now had two facials by Mara and each time my skin feels so refreshed and new! She has also helped my teenage son who has acne. Mara knew exactly what he needed and is already getting clearer skin. Worth every penny.
        <cite>PRIYA COLLINS - Mother of Five</cite>
        <span class="mark close">&rdquo;</span>
      </blockquote>

      <blockquote class="quote" style="left:72px; top:228px; width:200px;">
        <span class="mark open">&ldquo;</span>
        I've been seeing Mara on a regular basis because she always goes above and beyond to ensure that I'm comfortable. She made the experience all about me and my skincare needs. She is highly knowledgeable and offers creative options to make sure I get what I need.
        <cite>Jill Arbogast - marketing executive</cite>
        <span class="mark close">&rdquo;</span>
      </blockquote>

      <blockquote class="quote" style="left:320px; top:226px; width:200px;">
        <span class="mark open">&ldquo;</span>
        Having ethnic skin I've been hesitant about having treatments but Mara immediately put me at ease. She has taught me so much about my skin and how to care for it. Each time I've left with my skin looking and feeling amazing.
        <cite>TESSA MORLAND - Real Estate Agent</cite>
        <span class="mark close">&rdquo;</span>
      </blockquote>
    </section>
  </div>
</body>
</html>
```